Granola stand up bag packaging. Full Bleed printed on the bag. Full Color.

I Have a design I made but we are about to order thousands of printed bags so I thought I'd get a real designer to do the design. We do however want some sort of window area so the customer can see the granola through the bag. I have Illustrator native files of the logo for anyone who would like them. We have 3 flavors, so this is the first and we also have a coffee flavor, and a No BS flavor that we will need packaging for. The sample file is the package I designed myself, and like, however if we are going to pull the trigger on a $4,000 bag order then I want a design to use for the next 10 years!!

Target Market(s)

Granola Loving People at Natural Food Stores like Maple Crate.

Font styles to use
Sans Serif

Colors
acd036
ffffff
fbee3e

Requirements
Must have
• My logo, Some sort of transparent area so the customer can see the beautiful granola in the bag. Nutritional Facts and Bar Code area. Weight on the front of the bag.

```html
<!DOCTYPE html>
<html lang="en">
<head>
<meta charset="utf-8">
<title>Cascade Oat Company – Original Granola Bag</title>
<link rel="stylesheet" href="https://fonts.googleapis.com/css2?family=Roboto+Condensed:wght@400;700&family=Oswald:wght@500;700&family=Kaushan+Script&display=swap">
<style>
  :root {
    --lime: #acd036;
    --leaf: #5fa22c;
    --forest: #2f7a1f;
    --deep: #1f5a14;
    --sun: #fbee3e;
    --amber: #f2a81d;
    --orange: #e8881a;
    --white: #ffffff;
    --ink: #1a1a1a;
    --caption-grey: #8c8c8c;
    --stage: #ececec;
  }
  * { box-sizing: border-box; margin: 0; padding: 0; }
  html, body { width: 1200px; height: 1200px; overflow: hidden; }
  body {
    background: var(--white);
    font-family: "Roboto Condensed", sans-serif;
    color: var(--ink);
    position: relative;
  }
  .caption { position: absolute; left: 123px; top: 48px; }
  .caption-title { font-size: 26px; font-weight: 700; color: var(--caption-grey); }
  .caption-text { font-size: 26px; margin-top: 8px; }

  .stage {
    position: absolute; left: 0; top: 174px; width: 1200px; height: 1026px;
    background: radial-gradient(ellipse at 50% 30%, #ffffff 0%, var(--stage) 60%, #d4d4d4 100%);
  }

  .bag-front {
    position: absolute; left: 330px; top: 300px; width: 400px; height: 750px;
    overflow: hidden; border-radius: 6px;
    background: linear-gradient(90deg, var(--leaf) 0%, var(--lime) 22%, var(--sun) 50%, var(--lime) 78%, var(--leaf) 100%);
  }
  .bag-front::after {
    content: ""; position: absolute; left: 0; right: 0; bottom: 0; height: 40%;
    background: linear-gradient(180deg, rgba(47,122,31,0) 0%, var(--forest) 100%);
  }
  .center-band {
    position: absolute; left: 118px; width: 164px; top: 0; bottom: 0;
    background: linear-gradient(90deg, var(--sun) 0 10px, var(--amber) 10px 26px, var(--orange) 26px 138px, var(--amber) 138px 154px, var(--sun) 154px);
    opacity: .9;
  }
  .brand {
    position: absolute; z-index: 2; left: 0; right: 0; top: 130px;
    display: flex; align-items: center; justify-content: center; gap: 12px;
  }
  .brand-mark { width: 22px; height: 22px; border-radius: 50%; background: var(--white); flex: none; }
  .brand-name {
    font-family: "Roboto Condensed", sans-serif; font-weight: 700; font-size: 38px;
    line-height: 1.05; color: var(--white); text-align: left;
  }
  .claims {
    position: absolute; z-index: 2; left: 0; right: 0; top: 250px; text-align: center;
    font-family: "Roboto Condensed", sans-serif; font-weight: 700; font-size: 15px; letter-spacing: 1px;
    color: var(--white); text-transform: uppercase;
  }
  .tagline {
    position: absolute; z-index: 2; left: 90px; top: 318px;
    font-family: "Kaushan Script", cursive; color: var(--white);
    font-size: 44px; line-height: 40px;
  }
  .tagline span { display: block; }
  .tagline .amp { padding-left: 48px; font-size: 34px; }
  .tagline .word2 { padding-left: 46px; }
  .granola-bowl {
    position: absolute; z-index: 2; left: 40px; top: 462px; width: 320px; height: 172px;
    border-radius: 40px 40px 160px 160px / 40px 40px 130px 130px;
    background: radial-gradient(ellipse at 50% 25%, #d9a867 0%, #b07a3c 45%, #2b3d18 75%, #111 100%);
  }
  .flavor {
    position: absolute; z-index: 2; left: 96px; top: 652px; width: 208px; height: 44px;
    background: var(--white); display: flex; align-items: center; justify-content: center; gap: 8px;
    font-family: "Oswald", sans-serif; font-weight: 700; font-size: 30px; letter-spacing: 2px; color: var(--deep);
  }
  .flavor .dot { width: 8px; height: 8px; border-radius: 50%; background: var(--amber); }
  .net-weight {
    position: absolute; z-index: 2; left: 96px; top: 704px; width: 208px;
    font-weight: 700; font-size: 15px; line-height: 18px; letter-spacing: 1px; color: var(--white); text-align: center;
    border-bottom: 3px solid var(--amber); padding-bottom: 2px;
  }

  .bag-side {
    position: absolute; left: 746px; top: 300px; width: 170px; height: 750px;
    border-radius: 6px;
    background: linear-gradient(180deg, var(--lime) 0%, var(--leaf) 55%, var(--forest) 100%);
    padding: 150px 14px 0;
  }
  .nutrition {
    background: var(--white); border: 2px solid var(--ink); padding: 6px 7px;
    font-size: 10.5px; line-height: 1.35; color: var(--ink);
  }
  .nutrition h2 { font-family: "Oswald", sans-serif; font-size: 19px; font-weight: 700; line-height: 1.1; border-bottom: 1px solid var(--ink); padding-bottom: 3px; }
  .nutrition .thick { border-bottom: 5px solid var(--ink); }
  .nutrition .row { display: flex; justify-content: space-between; border-bottom: 1px solid var(--ink); }
  .nutrition .ingredients { margin-top: 5px; font-size: 9.5px; }
  .barcode-area { margin-top: 18px; height: 90px; background: var(--white); border: 2px solid var(--ink); }
</style>
</head>
<body>
  <header class="caption">
    <p class="caption-title">Adaptation for the same direction</p>
    <p class="caption-text">Customer can see the granola through back and front, product’s inforamtion are at both sides.</p>
  </header>

  <div class="stage"></div>

  <section class="bag-front">
    <div class="center-band"></div>
    <div class="brand">
      <span class="brand-mark"></span>
      <p class="brand-name">Cascade Oat<br>Company</p>
    </div>
    <p class="claims">Gluten-free · Vegan · Small-batch</p>
    <p class="tagline"><span>Healthy</span><span class="amp">&amp;</span><span class="word2">Natural</span></p>
    <div class="granola-bowl" role="img" aria-label="Window showing a bowl of golden oat granola with raisins"></div>
    <p class="flavor"><span class="dot"></span>Original<span class="dot"></span></p>
    <p class="net-weight">Net weight 12 oz (340g)</p>
  </section>

  <aside class="bag-side">
    <div class="nutrition">
      <h2>Nutrition Facts</h2>
      <p>Serving Size 1/3 cup (28g)</p>
      <p class="thick">Servings About 12</p>
      <div class="row"><b>Calories</b><b>130</b></div>
      <div class="row"><span>Total Fat 5g</span><span>8%</span></div>
      <div class="row"><span>Saturated Fat 0.5g</span><span>3%</span></div>
      <div class="row"><span>Sodium 35mg</span><span>1%</span></div>
      <div class="row"><span>Total Carbohydrate 19g</span><span>6%</span></div>
      <div class="row"><span>Dietary Fiber 2g</span><span>8%</span></div>
      <div class="row"><span>Sugars 7g</span><span></span></div>
      <div class="row thick"><span>Protein 3g</span><span></span></div>
      <div class="row"><span>Iron 6%</span><span>Calcium 2%</span></div>
      <p class="ingredients">Ingredients: oats, maple, raisins, coconut oil, sea salt.</p>
    </div>
    <div class="barcode-area"></div>
  </aside>
</body>
</html>
```